Email design required

We need a design for a paid B2B email campaign and facebook / retargeting banner ads that match the same style.

Website: http://pelmora.staging.hostvantry.com/
Campaign Name: KEX Weariness
Example: http://liftmarrowsites.com/kex-weariness/
- I made this over the weekend. It has the right words, but the style / layout needs to change

Size: 600 pixels wide, no limit on length

Formatting:
Format CSS inline only - This will ensure that size, font family, colour, line height, etc. will all remain the same once it is dropped into our newsletter sending software. See below as an

example,

Here's a mockup of

Target Market(s)

Canadian mortgage brokers

Industry/Entity Type

Campaign

Font styles to use
Sans Serif

Colors
3277b5

Requirements
Must have
• Text from my website example http://liftmarrowsites.com/kex-weariness/
• Otherwise, do whatever you think would look good.

```html
<!DOCTYPE html>
<html lang="en">
<head>
<meta charset="utf-8">
<title>Pelmora – KEX Weariness</title>
<link href="https://fonts.googleapis.com/css2?family=Open+Sans:ital,wght@0,400;0,600;0,700;1,400;1,600&display=swap" rel="stylesheet">
<style>
  :root {
    --page-bg: #2b2b2d;
    --brand-blue: #3277b5;
    --logo-blue: #1f6dbf;
    --hero-light: #0aa0ff;
    --hero-dark: #06256b;
    --orange: #f7931e;
    --white: #ffffff;
    --header-bg: #f7f7f7;
    --text-grey: #8a8a8a;
    --quote-grey: #8f8f8f;
    --table-dark: #262626;
    --table-mid: #3b3e48;
    --footer-bg: #45434f;
    --tick-green: #2bb98e;
    --avatar-grey: #545557;
  }
  * { box-sizing: border-box; margin: 0; padding: 0; }
  html, body {
    width: 960px; height: 1200px; overflow: hidden;
    background: var(--page-bg);
    font-family: "Open Sans", sans-serif;
  }
  .email {
    position: absolute; left: 242px; top: 102px; width: 480px;
    background: var(--white);
  }
  section, header, footer { position: relative; width: 100%; }

  .top-bar { height: 59px; background: var(--header-bg); }
  .brand {
    position: absolute; left: 22px; top: 14px;
    font-size: 21px; font-weight: 600; color: var(--logo-blue);
    display: flex; align-items: center; gap: 4px; letter-spacing: -0.3px;
  }
  .brand-square { width: 14px; height: 14px; background: var(--logo-blue); }
  .contact-link {
    position: absolute; right: 29px; top: 22px;
    font-size: 11px; color: var(--text-grey);
  }

  .hero {
    height: 207px;
    background: radial-gradient(ellipse 62% 80% at 52% 62%, var(--hero-light) 0%, #0766cf 45%, var(--hero-dark) 100%);
    color: var(--white);
  }
  .hero-title {
    position: absolute; top: 6px; width: 100%; text-align: center;
    font-size: 29px; font-weight: 700;
  }
  .hero-offer {
    position: absolute; left: 26px; top: 79px; width: 224px; text-align: center;
    font-size: 11.5px; line-height: 16px; font-weight: 600;
  }
  .hero-offer .price { color: var(--orange); }
  .hero-button {
    position: absolute; left: 58px; top: 130px; width: 144px; height: 34px;
    border-radius: 17px; background: var(--orange); color: var(--white);
    font-size: 11.5px; font-weight: 700; letter-spacing: 0.3px;
    display: flex; align-items: center; justify-content: center;
  }
  .hero-illustration {
    position: absolute; left: 274px; top: 62px; width: 144px; height: 116px;
    background: radial-gradient(circle at 55% 45%, rgba(255,255,255,0.35), rgba(255,255,255,0.08));
    border-radius: 6px;
  }

  .section-band {
    height: 38px; background: var(--brand-blue); color: var(--white);
    font-size: 13.5px; font-weight: 700; text-align: center; line-height: 38px;
  }
  .section-band.tall { height: 39px; line-height: 39px; }

  .review { height: 135px; }
  .reviewer-avatar {
    position: absolute; left: 47px; top: 14px; width: 100px; height: 100px;
    border-radius: 50%; background: var(--avatar-grey);
  }
  .review-quote {
    position: absolute; left: 198px; top: 22px; width: 256px;
    font-size: 10.4px; line-height: 16px; font-style: italic; color: var(--quote-grey);
  }
  .review-author {
    position: absolute; left: 198px; top: 91px;
    font-size: 10.4px; font-weight: 600; color: var(--quote-grey);
  }

  .compare { height: 370px; }
  .compare-head {
    position: absolute; top: 20px; font-weight: 700;
  }
  .compare-head.ours {
    left: 211px; font-size: 17px; color: var(--logo-blue); font-weight: 600;
    display: flex; align-items: center; gap: 3px; letter-spacing: -0.3px;
  }
  .compare-head.ours .brand-square { width: 12px; height: 12px; }
  .compare-head.theirs { left: 364px; top: 25px; font-size: 12px; color: #111; }

  .compare-table {
    position: absolute; left: 34px; top: 59px; width: 403px;
    font-size: 10.4px; color: var(--white);
  }
  .row { position: relative; display: flex; align-items: center; }
  .row.main { height: 27.5px; }
  .row.main:nth-child(odd) { background: var(--table-mid); }
  .row.main:nth-child(even) { background: var(--table-dark); }
  .row.subhead { height: 28px; color: #222; }
  .row.service { background: var(--table-dark); border-top: 1px solid #555; font-style: italic; }
  .row .icon { position: absolute; left: 4px; width: 11px; height: 11px; }
  .row .label { position: absolute; left: 26px; }
  .row.service .label { left: 35px; line-height: 14px; }
  .row .ours-cell { position: absolute; left: 222px; transform: translateX(-50%); font-weight: 700; }
  .row .theirs-cell { position: absolute; left: 363px; transform: translateX(-50%); }
  .row.service .ours-cell { width: 18px; height: 16px; }
  .row.service .theirs-cell { font-style: normal; }

  .cta {
    position: absolute; left: 112px; top: 288px; width: 255px; height: 61px;
    border-radius: 31px; background: var(--orange); color: var(--white);
    text-align: center; display: flex; flex-direction: column; justify-content: center;
  }
  .cta-main { font-size: 18px; font-weight: 700; letter-spacing: 0.6px; line-height: 22px; }
  .cta-sub { font-size: 11px; font-weight: 700; letter-spacing: 0.3px; line-height: 16px; }

  .about { height: 119px; }
  .about-photo {
    position: absolute; left: 35px; top: 14px; width: 129px; height: 90px;
    background: linear-gradient(135deg, #3e5580, #263a63 60%, #1d2c4d);
  }
  .about-text {
    position: absolute; left: 198px; top: 11px; width: 256px;
    font-size: 10.2px; line-height: 16px; color: var(--text-grey);
  }

  .footer {
    height: 38px; background: var(--footer-bg); color: var(--white);
    font-size: 10.4px; display: flex; align-items: center; justify-content: space-between;
    padding: 0 26px 0 23px;
  }
</style>
</head>
<body>
<main class="email">
  <header class="top-bar">
    <div class="brand"><span class="brand-square"></span>Pelmora</div>
    <span class="contact-link">Contact</span>
  </header>

  <section class="hero">
    <h1 class="hero-title">Experiencing KEX Weariness?</h1>
    <p class="hero-offer">Unlimited Notice of Assessment Orders<br>For Just <span class="price">$29 / Month</span></p>
    <a class="hero-button">Get Started Now</a>
    <div class="hero-illustration" role="img" aria-label="Illustration of a tired worker slumped over a desk on an office chair"></div>
  </section>

  <div class="section-band">Customer Reviews</div>
  <section class="review">
    <div class="reviewer-avatar" role="img" aria-label="Reviewer profile picture placeholder"></div>
    <p class="review-quote">I've used a few different services for this and Pelmora is by far the best. Fraction of the cost and I have the required docs within a couple of hours at most. Makes my life so much easier.</p>
    <p class="review-author">Marcus Delvane, Norbrook Calgary</p>
  </section>

  <div class="section-band tall">Compare KEX Services</div>
  <section class="compare">
    <div class="compare-head ours"><span class="brand-square"></span>Pelmora</div>
    <div class="compare-head theirs">‘Other Guys’</div>

    <div class="compare-table">
      <div class="row main">
        <svg class="icon" viewBox="0 0 12 12"><circle cx="6" cy="6" r="4.6" fill="none" stroke="#fff" stroke-width="1.4"/><path d="M3.5 6l2 2 5-5.5" fill="none" stroke="#fff" stroke-width="1.6"/></svg>
        <span class="label">Price</span><span class="ours-cell">$29 / month</span><span class="theirs-cell">$39 / Order</span>
      </div>
      <div class="row main">
        <svg class="icon" viewBox="0 0 12 12"><circle cx="6" cy="6" r="4.6" fill="none" stroke="#fff" stroke-width="1.4"/><path d="M3.5 6l2 2 5-5.5" fill="none" stroke="#fff" stroke-width="1.6"/></svg>
        <span class="label">Units</span><span class="ours-cell">Unlimited</span><span class="theirs-cell">Just One</span>
      </div>
      <div class="row main">
        <svg class="icon" viewBox="0 0 12 12"><circle cx="6" cy="6" r="4.6" fill="none" stroke="#fff" stroke-width="1.4"/><path d="M3.5 6l2 2 5-5.5" fill="none" stroke="#fff" stroke-width="1.6"/></svg>
        <span class="label">Turnaround</span><span class="ours-cell">4 Hours</span><span class="theirs-cell">1 Day</span>
      </div>
      <div class="row subhead">
        <svg class="icon" viewBox="0 0 12 12"><circle cx="6" cy="6" r="4.6" fill="none" stroke="#222" stroke-width="1.4"/><path d="M3.5 6l2 2 5-5.5" fill="none" stroke="#222" stroke-width="1.6"/></svg>
        <span class="label">Other Services</span>
      </div>
      <div class="row service" style="height:28px">
        <span class="label">Document Sorting</span>
        <svg class="ours-cell" viewBox="0 0 18 16"><rect x="1" y="3" width="12" height="12" fill="none" stroke="#888" stroke-width="1.2"/><path d="M3 9l4 4 10-12" fill="none" stroke="var(--tick-green)" stroke-width="2.6"/></svg>
        <span class="theirs-cell">x</span>
      </div>
      <div class="row service" style="height:30px">
        <span class="label">Lender Fulfillment</span>
        <svg class="ours-cell" viewBox="0 0 18 16"><rect x="1" y="3" width="12" height="12" fill="none" stroke="#888" stroke-width="1.2"/><path d="M3 9l4 4 10-12" fill="none" stroke="var(--tick-green)" stroke-width="2.6"/></svg>
        <span class="theirs-cell">x</span>
      </div>
      <div class="row service" style="height:34px">
        <span class="label">Closing Package Prepartion<br>And Much More</span>
        <svg class="ours-cell" viewBox="0 0 18 16"><rect x="1" y="3" width="12" height="12" fill="none" stroke="#888" stroke-width="1.2"/><path d="M3 9l4 4 10-12" fill="none" stroke="var(--tick-green)" stroke-width="2.6"/></svg>
        <span class="theirs-cell">x</span>
      </div>
    </div>

    <a class="cta"><span class="cta-main">GET STARTED NOW</span><span class="cta-sub">30-Day Money Back Guarantee</span></a>
  </section>

  <div class="section-band tall">About Us</div>
  <section class="about">
    <div class="about-photo" role="img" aria-label="Photo of office filing cabinets with the company name"></div>
    <p class="about-text">Pelmora provides on-demand administrative support for Mortgage Professionals across Canada. Everything from Notice of Assessment and Title Orders to inbound document sorting and lender fulfilment can be outsouced at a fraction of the cost of a full time administrator.</p>
  </section>

  <footer class="footer">
    <span>© Pelmora 2016 All rights reserved.</span>
    <span>Unsubscribe here</span>
  </footer>
</main>
</body>
</html>
```